Kelo Wave Mint Business cards

Logo, tag line and photo on card
Agent Name
Title
Address
Phone number
Email
Website
Make logo on one side large by rotating  to portrait format.  Keep the background of the logo white.

Contact Information for Business Card
Slogan; Making Every Wave Count

```html
<!DOCTYPE html>
<html lang="en">
<head>
<meta charset="utf-8">
<title>Kelo Wave Mint Business Cards</title>
<link href="https://fonts.googleapis.com/css2?family=Saira:wght@400;700;800&family=Mrs+Saint+Delafield&display=swap" rel="stylesheet">
<style>
  :root {
    --stage: #747474;
    --navy: #002561;
    --red: #c8101f;
    --white: #ffffff;
    --ink-grey: #6b6b6b;
    --faint: #ebebeb;
    --rule: #333333;
  }
  * { box-sizing: border-box; margin: 0; padding: 0; }
  html, body { width: 1200px; height: 1000px; overflow: hidden; }
  body { background: var(--stage); font-family: "Saira", sans-serif; position: relative; }

  .card { position: absolute; width: 613px; height: 352px; border-radius: 30px; overflow: hidden; }

  .card-front { left: 295px; top: 126px; background: var(--navy); }
  .brand-badge {
    position: absolute; left: 246px; top: 78px; width: 121px; height: 151px;
    background: var(--white); border: 4px solid var(--red); border-radius: 8px;
    display: flex; align-items: center; justify-content: center;
  }
  .brand-name {
    color: var(--navy); font-weight: 800; font-size: 31px; line-height: 1.05;
    text-align: center; letter-spacing: -0.5px;
  }
  .tagline {
    position: absolute; left: 0; right: 0; top: 250px; text-align: center;
    color: var(--white); font-family: "Mrs Saint Delafield", cursive; font-size: 50px;
  }

  .card-back { left: 294px; top: 538px; background: var(--white); }
  .faint-band {
    position: absolute; left: 246px; top: 0; width: 20px; height: 352px;
    background: var(--faint); transform: skewX(5deg);
  }
  .faint-name {
    position: absolute; left: 290px; top: 0; color: var(--faint);
    font-weight: 800; font-size: 118px; line-height: 0.98; letter-spacing: -2px;
  }
  .portrait {
    position: absolute; left: 48px; top: 35px; width: 116px; height: 116px;
    border-radius: 50%; border: 2px solid var(--red); padding: 4px; background: var(--white);
  }
  .portrait-fill {
    width: 100%; height: 100%; border-radius: 50%;
    background: radial-gradient(circle at 50% 45%, #a48a7a 0%, #7a7470 45%, #3d3b3b 100%);
  }
  .agent-name {
    position: absolute; left: 42px; top: 158px; color: var(--navy);
    font-weight: 700; font-size: 20px; letter-spacing: 1.6px;
  }
  .agent-title {
    position: absolute; left: 42px; top: 181px; color: var(--red);
    font-size: 18px; letter-spacing: 1px;
  }
  .divider { position: absolute; left: 42px; top: 213px; width: 152px; height: 1px; background: var(--rule); }
  .address {
    position: absolute; left: 42px; top: 227px; color: var(--ink-grey);
    font-size: 13px; letter-spacing: 1.2px;
  }
  .contact-list { position: absolute; left: 42px; top: 255px; list-style: none; }
  .contact-list li {
    display: flex; align-items: center; gap: 8px; height: 21.5px;
    color: var(--ink-grey); font-size: 17px;
  }
  .contact-list svg { width: 13px; height: 13px; fill: var(--red); flex: none; }
</style>
</head>
<body>

<section class="card card-front">
  <div class="brand-badge">
    <div class="brand-name">Kelo<br>Wave<br>Mint</div>
  </div>
  <p class="tagline">Making Every Wave Count</p>
</section>

<section class="card card-back">
  <div class="faint-band"></div>
  <div class="faint-name" aria-hidden="true">Kelo<br>Wave<br>Mint</div>

  <div class="portrait">
    <div class="portrait-fill" role="img" aria-label="Agent portrait photo"></div>
  </div>
  <h1 class="agent-name">AGENT NAME</h1>
  <p class="agent-title">TITLE</p>
  <div class="divider"></div>
  <p class="address">ADDRESS</p>
  <ul class="contact-list">
    <li>
      <svg viewBox="0 0 16 16"><path d="M3.6 1.2l2.3 2.6-1.3 1.8c.9 2 2.6 3.7 4.6 4.6l1.8-1.3 2.6 2.3-1.4 2.5C7 13.4 2.6 9 1.3 2.8z"/></svg>
      Phone number
    </li>
    <li>
      <svg viewBox="0 0 16 16"><path d="M1 3h14v10H1z M1.8 3.8L8 8.8l6.2-5" fill="var(--red)" stroke="var(--white)" stroke-width="1.2"/></svg>
      Email
    </li>
    <li>
      <svg viewBox="0 0 16 16"><circle cx="8" cy="8" r="7"/><path d="M1 8h14M8 1v14M3 4.2h10M3 11.8h10M8 1c-3 3.5-3 10.5 0 14M8 1c3 3.5 3 10.5 0 14" fill="none" stroke="var(--white)" stroke-width="1"/></svg>
      Website
    </li>
  </ul>
</section>

</body>
</html>
```